Personal Business Card design contest for freelance work

Include

Brenvola.net/in/DanielMWhitacre (as URL and/or QR Code)
Daniel Whitacre
(555) 218-9034
DanielMWhitacre@Pelmora.com
Houston, TX

Industry/Entity Type

Business

```html
<!DOCTYPE html>
<html lang="en">
<head>
<meta charset="utf-8">
<title>Daniel Whitacre – Business Card</title>
<link href="https://fonts.googleapis.com/css2?family=Open+Sans:wght@400;600&display=swap" rel="stylesheet">
<style>
  :root {
    --stage: #2a2a2c;
    --card-top: #232428;
    --card-bottom: #161719;
    --ink: #f2f2f2;
    --accent: #5fb0dc;
    --rule: #4a4d52;
    --art-front-a: #3a3c42;
    --art-front-b: #2c2e33;
    --art-back-a: #3b3c40;
    --art-back-b: #2a2b2e;
  }
  * { box-sizing: border-box; margin: 0; padding: 0; }
  html, body { width: 1200px; height: 844px; overflow: hidden; }
  body {
    background: var(--stage);
    font-family: "Open Sans", sans-serif;
    display: flex;
    align-items: center;
    justify-content: center;
    gap: 50px;
  }
  .card {
    position: relative;
    width: 540px;
    height: 309px;
    border-radius: 4px;
    background: linear-gradient(160deg, var(--card-top), var(--card-bottom));
    box-shadow: 0 14px 30px rgba(0,0,0,.45);
    overflow: hidden;
  }
  .card__art {
    position: absolute;
    left: 50%;
    transform: translateX(-50%);
    border-radius: 4px;
  }
  .card--front .card__art {
    top: 34px;
    width: 66px;
    height: 112px;
    background: linear-gradient(180deg, var(--art-front-a), var(--art-front-b));
  }
  .card--back .card__art {
    top: 52px;
    width: 116px;
    height: 205px;
    background: linear-gradient(180deg, var(--art-back-a), var(--art-back-b));
  }
  .card__identity {
    position: absolute;
    right: 286px;
    top: 176px;
    text-align: right;
    color: var(--ink);
  }
  .card__name { font-size: 27px; font-weight: 600; line-height: 1.1; white-space: nowrap; }
  .card__title { font-size: 14px; color: var(--accent); margin-top: 2px; }
  .card__address { font-size: 15px; margin-top: 10px; line-height: 1.35; }
  .card__divider {
    position: absolute;
    left: 268px;
    top: 166px;
    width: 1px;
    height: 100px;
    background: var(--rule);
  }
  .card__contacts {
    position: absolute;
    left: 284px;
    top: 174px;
    list-style: none;
    color: var(--ink);
    font-size: 12.5px;
  }
  .card__contacts li {
    display: flex;
    align-items: center;
    gap: 8px;
    line-height: 25px;
    white-space: nowrap;
  }
  .card__icon { width: 11px; height: 11px; fill: var(--accent); flex: none; }
</style>
</head>
<body>
  <section class="card card--front">
    <div class="card__art" role="img" aria-label="Small caricature illustration of Daniel Whitacre"></div>
    <div class="card__identity">
      <p class="card__name">Daniel Whitacre</p>
      <p class="card__title">Managing Director</p>
      <p class="card__address">Houston, TX</p>
    </div>
    <div class="card__divider"></div>
    <ul class="card__contacts">
      <li>
        <svg class="card__icon" viewBox="0 0 12 12"><path d="M2.4 1h2l1 2.6-1.3 1a6.5 6.5 0 0 0 3.3 3.3l1-1.3 2.6 1v2a1 1 0 0 1-1 1A9.6 9.6 0 0 1 1.4 2a1 1 0 0 1 1-1z"/></svg>
        (555) 218-9034
      </li>
      <li>
        <svg class="card__icon" viewBox="0 0 12 12"><path d="M1 2.5h10v7H1z M1.6 3l4.4 3.5L10.4 3" fill="none" stroke="#5fb0dc" stroke-width="1.2"/></svg>
        DanielMWhitacre@Pelmora.com
      </li>
      <li>
        <svg class="card__icon" viewBox="0 0 12 12"><path d="M5 7l2-2M4.2 5.3 2.6 6.9a1.8 1.8 0 0 0 2.5 2.5l1.6-1.6M7.8 6.7l1.6-1.6a1.8 1.8 0 0 0-2.5-2.5L5.3 4.2" fill="none" stroke="#5fb0dc" stroke-width="1.3" stroke-linecap="round"/></svg>
        Brenvola.net/in/DanielMWhitacre
      </li>
    </ul>
  </section>

  <section class="card card--back">
    <div class="card__art" role="img" aria-label="Large monochrome caricature illustration of Daniel Whitacre"></div>
  </section>
</body>
</html>
```